Website for BrightlineLabs presentation

We need a new website, ideally as a wordpress there, for BrightlineLabs - we focus on machine learning, big data, data science and data analytics. This website should have two main sections - team presentation, introduction and offered services as static pages, and a blog section.

Target Market(s)

Companies which would like to hire the consultants for data science

Industry/Entity Type

Data Service

Font styles to use
Sans Serif

Colors

Designer to choose colors to be used in the design.

Requirements
Must have
• Wordpress template, blog and presentation pages, nice background images, incorporate the existing logo from brief
Nice to have
• match the word and ppt existing templates for brightline labs

```html
<!DOCTYPE html>
<html lang="en">
<head>
<meta charset="utf-8">
<title>Brightline Labs</title>
<link href="https://fonts.googleapis.com/css2?family=Open+Sans:wght@400;600;700&family=Raleway:wght@400;500;600&family=Roboto+Condensed:wght@400;700&display=swap" rel="stylesheet">
<style>
:root{
  --brand:#1c6fb8;
  --brand-light:#2a8ad6;
  --navy:#0c2463;
  --navy-mid:#173f93;
  --night:#070d1c;
  --ink:#222;
  --muted:#555;
  --line:#d9d9d9;
  --white:#fff;
  --footer:#141414;
  --gold:#e2a93b;
}
*{box-sizing:border-box;margin:0;padding:0}
html,body{width:1200px;height:4138px;overflow:hidden}
body{font-family:'Open Sans',sans-serif;color:var(--ink);background:var(--white);position:relative}
.abs{position:absolute}
a{color:inherit;text-decoration:none}

/* header */
.site-header{position:absolute;left:0;top:0;width:1200px;height:116px;background:var(--white)}
.brand{position:absolute;left:91px;top:22px;display:flex;align-items:center;gap:12px}
.brand-dot{width:38px;height:38px;border-radius:50%;background:var(--brand)}
.brand-name{font-family:'Open Sans',sans-serif;font-weight:700;font-size:19px;line-height:21px;color:var(--brand);width:130px}
.main-nav{position:absolute;top:48px;left:452px;display:flex;gap:0}
.main-nav a{font-size:16px;color:#333;margin-right:40px;text-transform:uppercase}
.main-nav a.active{color:var(--brand)}
.search-icon{position:absolute;left:1090px;top:49px}

/* hero */
.hero{position:absolute;left:0;top:116px;width:1200px;height:607px;background:radial-gradient(circle at 72% 35%,#3a8fd8 0%,#134a8f 16%,#0a1d3e 34%,var(--night) 60%)}
.hero-title{position:absolute;left:88px;top:222px;font-family:'Roboto Condensed',sans-serif;font-size:56px;color:var(--white);font-weight:400}
.hero-sub{position:absolute;left:88px;top:296px;font-family:'Roboto Condensed',sans-serif;font-size:28px;color:var(--white)}

/* welcome */
.welcome-frame{position:absolute;left:102px;top:850px;width:353px;height:254px;border:2px solid #444}
.welcome-media{position:absolute;left:127px;top:872px;width:381px;height:331px;background:linear-gradient(135deg,#0a2a14,#0c3a1c 45%,#073f5c 70%,#021008)}
.welcome-title{position:absolute;left:557px;top:910px;font-family:'Raleway',sans-serif;font-size:37px;color:#222;font-weight:500}
.welcome-title span{color:var(--brand)}
.welcome-text{position:absolute;left:557px;top:962px;width:543px;font-size:15px;line-height:30px;color:var(--muted);text-align:justify}
.btn-read{position:absolute;left:566px;top:1148px;width:99px;height:27px;border-radius:14px;background:var(--brand);color:var(--white);font-size:13px;line-height:27px;text-align:center}

/* services */
.services{position:absolute;left:0;top:1330px;width:1200px;height:643px;background:radial-gradient(circle at 55% 30%,#2458b8,var(--navy-mid) 45%,var(--navy) 100%)}
.section-title{position:absolute;left:0;width:1200px;text-align:center;font-family:'Raleway',sans-serif;font-size:38px;font-weight:400}
.service-card{position:absolute;width:236px;height:252px;background:var(--white);text-align:center;box-shadow:0 4px 10px rgba(0,0,0,.25)}
.service-icon{position:absolute;left:78px;top:-40px;width:80px;height:80px;border-radius:50%;background:var(--brand);border:5px solid var(--white);display:flex;align-items:center;justify-content:center}
.service-card h3{margin-top:66px;font-size:16px;font-weight:600;color:#222}
.service-card p{margin:16px auto 0;width:190px;font-size:12.5px;line-height:19px;color:#666}
.service-card .more{display:inline-block;margin-top:16px;font-size:13px;font-weight:600;color:#222;border-bottom:2px solid var(--gold);padding-bottom:5px}

/* team */
.team-card{position:absolute;width:315px;height:381px;background:var(--white);box-shadow:0 0 8px rgba(0,0,0,.25);text-align:center}
.avatar{position:absolute;left:94px;top:31px;width:127px;height:127px;border-radius:50%;background:linear-gradient(160deg,#d7d2cc,#8a8176);border:4px solid #eee}
.team-card h3{position:absolute;top:172px;left:0;width:100%;font-size:19px;font-weight:600;color:#222}
.team-card p{position:absolute;top:215px;left:36px;width:243px;font-size:16px;line-height:30px;color:#333}
.socials{position:absolute;top:322px;left:0;width:100%;display:flex;justify-content:center;gap:8px}
.socials span{width:27px;height:27px;border-radius:50%;background:var(--brand)}

/* testimonial */
.testimonial{position:absolute;left:0;top:2662px;width:1200px;height:511px;background:radial-gradient(circle at 40% 40%,#2453b0,var(--navy-mid) 50%,var(--navy) 100%)}
.quote-avatar{position:absolute;left:174px;top:182px;width:144px;height:144px;border-radius:50%;background:linear-gradient(160deg,#c9b8a4,#6a5a4a);border:4px solid var(--white)}
.quote-box{position:absolute;left:251px;top:163px;width:737px;height:193px;border:3px solid var(--white);padding:26px 40px 0 110px;color:var(--white);font-size:14.5px;line-height:27px}
.quote-mark{position:absolute;left:76px;top:22px;font-size:40px;font-family:Georgia,serif;line-height:1}
.quote-author{font-style:italic}

/* blog */
.blog-card{position:absolute;width:312px}
.blog-img{width:312px;height:174px}
.blog-meta{margin-top:24px;display:flex;height:19px}
.blog-date{background:var(--navy);color:var(--white);font-size:11px;line-height:19px;padding:0 16px}
.blog-com{background:#222;width:36px}
.blog-card h3{margin-top:14px;font-size:16px;font-weight:400;color:#222}
.blog-card p{margin-top:8px;font-size:12.5px;line-height:19px;color:#666;width:300px}
.blog-card .blog-more{display:block;margin-top:10px;font-size:12.5px;color:var(--brand)}

/* footer */
.footer-social{position:absolute;top:3847px;left:965px;display:flex;gap:12px}
.footer-social span{width:27px;height:27px;border-radius:4px;background:#bbb}
.footer-brand{position:absolute;left:102px;top:3925px;display:flex;align-items:center;gap:14px}
.footer-brand .brand-name{color:var(--brand-light);font-size:23px;line-height:26px;width:160px}
.newsletter-label{position:absolute;left:612px;top:3964px;color:var(--white);font-size:15px}
.newsletter-input{position:absolute;left:828px;top:3951px;width:281px;height:47px;border:2px solid #ccc;border-radius:24px;color:#ddd;font-size:13px;line-height:43px;padding-left:24px}
.newsletter-go{position:absolute;right:14px;top:12px;width:18px;height:18px;border-radius:50%;background:#ccc}
.footer-rule{position:absolute;left:88px;top:4042px;width:1022px;height:1px;background:#555}
.footer-links{position:absolute;left:91px;top:4066px;display:flex;gap:26px;color:var(--white);font-size:14px}
.copyright{position:absolute;left:866px;top:4068px;color:var(--white);font-size:13px}
</style>
</head>
<body>

<header class="site-header">
  <div class="brand"><span class="brand-dot"></span><span class="brand-name">BRIGHTLINE LABS</span></div>
  <nav class="main-nav">
    <a class="active" href="#">Home</a><a href="#">About Us</a><a href="#">Services</a><a href="#">Team</a><a href="#">Blog</a><a href="#">Contact</a>
  </nav>
  <svg class="search-icon" width="18" height="18" viewBox="0 0 18 18"><circle cx="7.5" cy="7.5" r="5.5" fill="none" stroke="#222" stroke-width="2.6"/><line x1="11.5" y1="11.5" x2="16.5" y2="16.5" stroke="#222" stroke-width="3"/></svg>
</header>

<section class="hero" role="img" aria-label="Glowing digital globe of network points touched by a hand on a dark background">
  <h1 class="hero-title">Brightline Labs</h1>
  <p class="hero-sub">Neque porro quisquam est dolorem</p>
</section>
<svg class="abs" style="left:0;top:620px" width="1200" height="104" viewBox="0 0 1200 104">
  <polygon points="0,104 0,94 1200,60 1200,104" fill="#fff"/>
  <polygon points="540,104 1200,20 1200,104" fill="#1c6fb8"/>
  <polygon points="0,104 0,96 560,104" fill="#fff"/>
</svg>

<div class="welcome-frame"></div>
<div class="welcome-media" role="img" aria-label="Glowing laboratory flask over green digital code"></div>
<h2 class="welcome-title">Welcome to <span>Brightline Labs</span></h2>
<p class="welcome-text">It is a long established fact that a reader will be distracted by the readable content of a page when looking at its layout. The point of using Lorem Ipsum is that it has a more-or-less normal distribution of letters, as opposed to using 'Content here, content here', making it look like readable English. Many desktop publishing packages It is a long established fact that a reader will be distracted by the readable content of a page</p>
<a class="btn-read" href="#">Read More</a>

<section class="services">
  <h2 class="section-title" style="top:68px;color:#fff">Our Services</h2>
  <div class="service-card" style="left:94px;top:220px">
    <div class="service-icon"><svg width="30" height="30" viewBox="0 0 30 30"><circle cx="15" cy="15" r="10" fill="none" stroke="#fff" stroke-width="5" stroke-dasharray="4 3"/><circle cx="15" cy="15" r="4" fill="#fff"/></svg></div>
    <h3>Machine Learning</h3>
    <p>It is a long established fact that a reader will be tracted by the readable content of a page when looking</p>
    <a class="more" href="#">READ MORE</a>
  </div>
  <div class="service-card" style="left:356px;top:220px">
    <div class="service-icon"><svg width="26" height="30" viewBox="0 0 26 30"><ellipse cx="13" cy="5" rx="11" ry="4" fill="#fff"/><rect x="2" y="9" width="22" height="7" rx="3" fill="#fff"/><rect x="2" y="18" width="22" height="8" rx="3" fill="#fff"/></svg></div>
    <h3>Big Data</h3>
    <p>It is a long established fact that a reader will be tracted by the readable content of a page when looking</p>
    <a class="more" href="#">READ MORE</a>
  </div>
  <div class="service-card" style="left:615px;top:222px">
    <div class="service-icon"><svg width="30" height="28" viewBox="0 0 30 28"><rect x="2" y="2" width="26" height="18" rx="2" fill="none" stroke="#fff" stroke-width="3"/><rect x="11" y="22" width="8" height="4" fill="#fff"/></svg></div>
    <h3>Data Science</h3>
    <p>It is a long established fact that a reader will be tracted by the readable content of a page when looking</p>
    <a class="more" href="#">READ MORE</a>
  </div>
  <div class="service-card" style="left:875px;top:224px">
    <div class="service-icon"><svg width="24" height="30" viewBox="0 0 24 30"><path d="M2 2h14l6 6v20H2z" fill="#fff"/><rect x="6" y="14" width="12" height="2" fill="#1c6fb8"/><rect x="6" y="19" width="12" height="2" fill="#1c6fb8"/></svg></div>
    <h3>Data Analytics</h3>
    <p>It is a long established fact that a reader will be tracted by the readable content of a page when looking</p>
    <a class="more" href="#">READ MORE</a>
  </div>
</section>
<svg class="abs" style="left:0;top:1850px" width="1200" height="124" viewBox="0 0 1200 124">
  <polygon points="0,40 440,124 0,124" fill="#111"/>
  <polygon points="0,124 1200,124 1200,70 0,124" fill="#fff"/>
</svg>

<h2 class="section-title" style="top:2068px;color:#222">Our Team</h2>
<div class="team-card" style="left:102px;top:2168px">
  <div class="avatar" role="img" aria-label="Portrait of team member"></div>
  <h3>Porro quisquam</h3>
  <p>It is a long established fact that a reader will be distracted by the readable content of a page</p>
  <div class="socials"><span></span><span></span><span></span></div>
</div>
<div class="team-card" style="left:447px;top:2168px">
  <div class="avatar" role="img" aria-label="Portrait of team member"></div>
  <h3>Dolorem ipsum</h3>
  <p>It is a long established fact that a reader will be distracted by the readable content of a page</p>
  <div class="socials"><span></span><span></span><span></span></div>
</div>
<div class="team-card" style="left:789px;top:2168px">
  <div class="avatar" role="img" aria-label="Portrait of team member"></div>
  <h3>Neque porro</h3>
  <p>It is a long established fact that a reader will be distracted by the readable content of a page</p>
  <div class="socials"><span></span><span></span><span></span></div>
</div>

<section class="testimonial">
  <h2 class="section-title" style="top:68px;color:#fff">Testimonial</h2>
  <div class="quote-box">
    <span class="quote-mark">&ldquo;</span>
    The point of using Lorem Ipsum is that it has a more-or-less normal distribution of letters, as opposed to using 'Content here, content here', making it look like readable English. Many desktop publishing packages and web page editors now use Lorem Ipsum as their default model text, and a search for 'lorem ipsum' will uncover many .<br>
    <span class="quote-author">- porro quisquam</span>
  </div>
  <div class="quote-avatar" role="img" aria-label="Portrait of client"></div>
  <svg class="abs" style="left:926px;top:382px" width="60" height="16" viewBox="0 0 60 16">
    <line x1="4" y1="8" x2="22" y2="8" stroke="#7fa4d8" stroke-width="3"/><polyline points="10,3 4,8 10,13" fill="none" stroke="#7fa4d8" stroke-width="3"/>
    <line x1="34" y1="8" x2="56" y2="8" stroke="#fff" stroke-width="3"/><polyline points="50,3 56,8 50,13" fill="none" stroke="#fff" stroke-width="3"/>
  </svg>
</section>
<svg class="abs" style="left:0;top:3060px" width="1200" height="114" viewBox="0 0 1200 114">
  <polygon points="0,114 0,100 1200,40 1200,114" fill="#fff"/>
  <polygon points="560,78 1200,0 1200,46" fill="#1c6fb8"/>
</svg>

<h2 class="section-title" style="top:3266px;color:#222">Latest Blog</h2>
<article class="blog-card" style="left:97px;top:3371px">
  <div class="blog-img" role="img" aria-label="Person walking through a server room aisle" style="background:linear-gradient(180deg,#1b3b66,#5b8fc4 50%,#0f2340)"></div>
  <div class="blog-meta"><span class="blog-date">Dec 03</span><span class="blog-com"></span></div>
  <h3>Neque porro quisquam dolorem</h3>
  <p>It has survived not only five centuries, but also the leap into electronic typesetting.</p>
  <a class="blog-more" href="#">Read More &raquo;</a>
</article>
<article class="blog-card" style="left:444px;top:3371px">
  <div class="blog-img" role="img" aria-label="Hand pointing at a digital data interface" style="background:linear-gradient(135deg,#d9dfe4,#a7b3bd 50%,#c48a58)"></div>
  <div class="blog-meta"><span class="blog-date">Dec 03</span><span class="blog-com"></span></div>
  <h3>Porro quisquam est qui</h3>
  <p>It has survived not only five centuries, but also the leap into electronic typesetting.</p>
  <a class="blog-more" href="#">Read More &raquo;</a>
</article>
<article class="blog-card" style="left:797px;top:3371px">
  <div class="blog-img" role="img" aria-label="Big data concept with glowing blue charts" style="background:linear-gradient(135deg,#5fb7e6,#2b87c8 50%,#cfe8f6)"></div>
  <div class="blog-meta"><span class="blog-date">Dec 03</span><span class="blog-com"></span></div>
  <h3>Dolorem ipsum quia dolor</h3>
  <p>It has survived not only five centuries, but also the leap into electronic typesetting.</p>
  <a class="blog-more" href="#">Read More &raquo;</a>
</article>

<footer>
  <svg class="abs" style="left:0;top:3760px" width="1200" height="378" viewBox="0 0 1200 378">
    <polygon points="0,110 1200,0 1200,378 0,378" fill="#141414"/>
    <polygon points="0,56 480,110 0,140" fill="#1c6fb8"/>
  </svg>
  <div class="footer-social"><span></span><span></span><span></span><span></span></div>
  <div class="footer-brand"><span class="brand-dot" style="width:50px;height:50px;background:#2a8ad6"></span><span class="brand-name">BRIGHTLINE LABS</span></div>
  <div class="newsletter-label">JOIN OUR NEWSLETTER</div>
  <div class="newsletter-input">Email address<span class="newsletter-go"></span></div>
  <div class="footer-rule"></div>
  <nav class="footer-links"><a href="#">Home</a><a href="#">About us</a><a href="#">Services</a><a href="#">Team</a><a href="#">Blog</a><a href="#">Contact</a></nav>
  <div class="copyright">Copyright &copy; 2018, All Rights Reserved</div>
</footer>

</body>
</html>
```